Black Matte card with samurai logo which I would like it to be textured and company name on one side and on the other side I would like the company information with the reno (Face logo) Sushi logo. Double Sided card.

majority customers are University students, University sororities and fraternities.

It Company

Reno Sushi
317 W. Harlow Ave
Tucson, AZ 85042
Phone (520)413-6271
Fax (520)357-1846
E-mail: Renosushidesert@mailbox-example.com
FB: Renosushidesert
Twitter: Renosushidesert

• Present Normal

```html
<!DOCTYPE html>
<html lang="en">
<head>
<meta charset="utf-8">
<title>Reno Sushi – Business Card</title>
<link rel="stylesheet" href="https://fonts.googleapis.com/css2?family=Advent+Pro:wght@400;500&display=swap">
<style>
  :root {
    --page: #ffffff;
    --card: #070808;
    --accent: #e8141b;
    --rule: #a3141b;
    --ink: #f2f2f2;
  }
  * { margin: 0; padding: 0; box-sizing: border-box; }
  html, body {
    width: 1200px;
    height: 702px;
    overflow: hidden;
    background: var(--page);
  }
  .card {
    position: absolute;
    left: 44px;
    top: 42px;
    width: 1111px;
    height: 617px;
    background: var(--card);
    font-family: "Advent Pro", sans-serif;
    color: var(--ink);
  }
  .brand {
    position: absolute;
    left: 40px;
    top: 92px;
    display: flex;
    align-items: center;
    gap: 26px;
  }
  .brand-name {
    font-family: "Advent Pro", sans-serif;
    font-weight: 500;
    font-size: 92px;
    line-height: 1;
    color: var(--accent);
    letter-spacing: 2px;
  }
  .brand-dot {
    width: 52px;
    height: 52px;
    border-radius: 50%;
    background: var(--accent);
  }
  .contact {
    position: absolute;
    left: 742px;
    top: 295px;
    height: 295px;
    padding-left: 30px;
    border-left: 4px solid var(--rule);
    font-weight: 400;
  }
  .contact-name {
    font-size: 33px;
    line-height: 1;
    margin-top: 20px;
  }
  .contact-line {
    font-size: 20px;
    line-height: 29px;
  }
  .contact-address { margin-top: 4px; margin-bottom: 30px; }
</style>
</head>
<body>
  <div class="card">
    <div class="brand">
      <span class="brand-name">reno sushi</span>
      <span class="brand-dot"></span>
    </div>
    <div class="contact">
      <p class="contact-name">Reno Sushi</p>
      <p class="contact-line contact-address">317 W. Harlow Ave Tucson, AZ 85042</p>
      <p class="contact-line">Phone (520)413-6271</p>
      <p class="contact-line">Fax (520)357-1846</p>
      <p class="contact-line">E-mail: Renosushidesert@mailbox-example.com</p>
      <p class="contact-line">FB: Renosushidesert</p>
      <p class="contact-line">Twitter: Renosushidesert</p>
    </div>
  </div>
</body>
</html>
```